Podiatry clinic requires a modern revamp and editing of existing website.

I would like a fresh new look and updated information for my current business website. An easy to navigate site with prominent address and phone number for call to action. We are a podiatry clinic that focuses on general and sports podiatry.
I would like 4 pages; including Home page, About Us, Services & Contact.
www.brambleridgepodiatry.net

Target Market(s)

Active working professionals.

Industry/Entity Type

Medical

Coding

Coded - Design and coding required

Number of Pages Required

4 page

Font styles to use
Sans Serif

Colors
6b449b

Requirements
Must have
• A modern look with logo and active images; clean and uncluttered. Visible phone number and address for call to action.
• 4 pages - Home, About Us, Services, Contact.
• Home page - update address & service logos.
• About Us - update of personal information.
• Services - Revamp of existing page.
• Contact page to include Google map, email & phone number.
Nice to have
• Ability to add content easily; eg. a blog or adding video onto Home page.
• Link to Chatterbook page.

```html
<!DOCTYPE html>
<html lang="en">
<head>
<meta charset="utf-8">
<title>Brambleridge Podiatry</title>
<link rel="stylesheet" href="https://fonts.googleapis.com/css2?family=Raleway:wght@300;400;600;700&family=Open+Sans:wght@400;600;700&display=swap">
<style>
:root{
  --purple:#4b2e9a;
  --purple-light:#5c3fc0;
  --purple-text:#3f2a8c;
  --grey-text:#555;
  --heading-grey:#555;
  --rule:#d6d6d6;
  --footer:#323232;
  --footer-bottom:#262626;
  --white:#fff;
  --panel:#eeeeee;
}
*{box-sizing:border-box;margin:0;padding:0}
html,body{width:1200px;height:2525px;overflow:hidden;background:var(--white)}
body{font-family:"Open Sans",Arial,sans-serif;color:var(--grey-text)}
.page{position:relative;width:1200px;height:2525px;overflow:hidden}
.abs{position:absolute}

/* hero */
.hero{left:0;top:0;width:1200px;height:640px;
  background:linear-gradient(180deg,#3c4a5c 0%,#6b7788 35%,#8a7f72 62%,#4a403a 100%)}
.logo-disc{left:77px;top:18px;width:260px;height:260px;border-radius:50%;background:var(--white);
  display:flex;align-items:center;justify-content:center;text-align:center}
.logo-name{font-family:"Raleway",Arial,sans-serif;font-weight:700;font-size:30px;line-height:1.2;color:var(--purple)}
.nav{right:79px;top:44px;display:flex;gap:46px;font-family:"Raleway",Arial,sans-serif;font-size:19px;color:var(--white);letter-spacing:.3px}
.hero-title{right:79px;top:176px;text-align:right;font-family:"Open Sans",Arial,sans-serif;font-weight:700;font-size:47px;line-height:78px;color:var(--white)}
.hero-sub{right:79px;top:358px;width:360px;text-align:right;font-size:21px;line-height:31px;color:var(--white)}
.hero-btn{left:894px;top:490px;width:228px;height:61px;border-radius:31px;background:var(--white);color:var(--purple);
  font-family:"Raleway",Arial,sans-serif;font-size:25px;display:flex;align-items:center;justify-content:center}

/* contact band */
.band-left{left:0;top:640px;width:473px;height:156px;background:var(--purple-light)}
.band-right{left:473px;top:640px;width:727px;height:156px;background:var(--purple)}
.band-lead{left:109px;top:664px;font-family:"Raleway",Arial,sans-serif;font-size:33px;line-height:52px;color:var(--white)}
.band-call{left:513px;top:668px;display:flex;align-items:center;gap:14px;color:var(--white);font-family:"Raleway",Arial,sans-serif;font-size:31px}
.band-call .num{font-family:"Open Sans",Arial,sans-serif;font-weight:700;font-size:31px;margin-left:6px}
.band-email{left:513px;top:730px;color:var(--white);font-size:21px}
.band-email span{margin-right:30px}

/* sections */
.section-title{left:0;width:1200px;text-align:center;font-family:"Raleway",Arial,sans-serif;font-weight:400;font-size:44px;color:var(--heading-grey)}
.section-title em{font-style:normal;color:var(--purple-text)}
.intro{left:210px;top:918px;width:780px;text-align:center;font-size:15.5px;line-height:26px;color:var(--grey-text)}
.btn{background:var(--purple);color:var(--white);border-radius:26px;font-family:"Raleway",Arial,sans-serif;font-size:22px;
  display:flex;align-items:center;justify-content:center}
.rule{left:77px;width:1046px;height:1px;background:var(--rule)}
.photo-foot{left:0;top:985px;width:353px;height:210px;border-radius:0 120px 60px 0;
  background:linear-gradient(120deg,#e9c2a8 0%,#f1d6c4 55%,rgba(255,255,255,0) 100%)}

.service-title{font-family:"Raleway",Arial,sans-serif;font-weight:400;font-size:32px;color:var(--purple-text)}
.service-photo{width:209px;height:142px}
.service-text{font-size:15px;line-height:26px;color:var(--grey-text)}

.news-photo{width:234px;height:145px}
.news-title{width:240px;font-size:17px;line-height:26px;color:var(--purple-text);letter-spacing:-.2px}
.news-date{font-size:14px;color:#888;display:flex;align-items:center;gap:6px}
.news-text{width:234px;font-size:15px;line-height:25px;color:var(--grey-text)}

.seen{left:77px;top:1969px;width:1046px;height:155px;background:var(--panel);box-shadow:0 22px 24px -14px rgba(0,0,0,.25)}
.seen-label{left:77px;top:1969px;width:270px;height:155px}
.seen-text{left:77px;top:1992px;width:200px;text-align:center;font-family:"Raleway",Arial,sans-serif;font-size:31px;line-height:42px;color:var(--white)}
.partner{top:2020px;height:52px;border-radius:6px;background:#d3d3d3}

/* footer */
.footer-curve{left:0;top:2180px}
.footer{left:0;top:2214px;width:1200px;height:257px;background:var(--footer)}
.footer-name{left:84px;top:2270px;width:230px;font-family:"Raleway",Arial,sans-serif;font-weight:600;font-size:34px;line-height:44px;color:#9a9a9a}
.footer-head{top:2250px;font-family:"Raleway",Arial,sans-serif;font-weight:400;font-size:22px;color:#e6e6e6}
.footer-list{top:2292px;list-style:none;font-size:17px;color:var(--white)}
.footer-list li{height:36px;display:flex;align-items:center;gap:10px}
.contact-list li{height:auto;align-items:flex-start;margin-bottom:14px;line-height:24px;font-size:16px}
.social li{height:auto;margin-bottom:20px;gap:14px}
.social .ring{width:47px;height:47px;border-radius:50%;background:var(--white);display:flex;align-items:center;justify-content:center;flex:none}
.social .ring.outline{background:none;border:2px solid var(--white)}
.copyright{left:0;top:2471px;width:1200px;height:54px;background:var(--footer-bottom);color:#ddd;font-size:16px;
  display:flex;align-items:center;justify-content:center}
</style>
</head>
<body>
<div class="page">

  <!-- hero -->
  <div class="abs hero" role="img" aria-label="Runner's legs in running shoes on an open desert road under a cloudy sky"></div>
  <div class="abs logo-disc"><div class="logo-name">Brambleridge<br>Podiatry</div></div>
  <nav class="abs nav"><span>HOME</span><span>ABOUT</span><span>SERVICES</span><span>CONTACT</span></nav>
  <h1 class="abs hero-title">QUALIFIED HEALTH<br>PROFESSIONALS</h1>
  <p class="abs hero-sub">Various foot conditions, including Sports Injuries, Orthotic Therapy &amp; Nail Surgery</p>
  <div class="abs hero-btn">CONTACT US</div>

  <!-- contact band -->
  <div class="abs band-left"></div>
  <div class="abs band-right"></div>
  <p class="abs band-lead">For Appointments or<br>Enquiries</p>
  <div class="abs band-call">
    <span>Please call us on</span>
    <svg width="54" height="54" viewBox="0 0 54 54" aria-hidden="true">
      <circle cx="27" cy="27" r="25" fill="none" stroke="#fff" stroke-width="2.5"/>
      <path d="M19 16c2-1 3 0 4 2l2 4c.6 1.3 0 2.2-1 3l-1 1c1 3 4 6 7 7l1-1c.8-1 1.7-1.6 3-1l4 2c2 1 3 2 2 4-1 3-4 4-7 3-7-2-13-8-15-15-1-3 0-6 1-9z" fill="#fff"/>
    </svg>
    <span class="num">1300 555 204</span>
  </div>
  <p class="abs band-email"><span>Email:</span>info@brambleridgepodiatry.net</p>

  <!-- welcome -->
  <div class="abs photo-foot" role="img" aria-label="Hands gently holding a bare foot"></div>
  <h2 class="abs section-title" style="top:840px">WELCOME TO <em>BRAMBLERIDGE PODIATRY</em></h2>
  <p class="abs intro">Brambleridge Podiatry is a Podiatry clinic in the heart of Melbourne CBD. We are located between Harlow &amp; Penfold Streets in the Larkspur Business Centre / Wren Hotel Complex.</p>
  <div class="abs btn" style="left:505px;top:991px;width:190px;height:50px">READ MORE</div>
  <div class="abs rule" style="top:1096px"></div>

  <!-- services -->
  <h2 class="abs section-title" style="top:1135px">SERVICES <em>WE PROVIDE</em></h2>

  <h3 class="abs service-title" style="left:79px;top:1213px">General Treatment</h3>
  <div class="abs service-photo" style="left:77px;top:1272px;background:linear-gradient(135deg,#f4f4f4,#dcdfe3 60%,#e8c9b4)" role="img" aria-label="Podiatrist in gloves examining a patient's foot"></div>
  <p class="abs service-text" style="left:298px;top:1270px;width:295px">Nails, Corns, Callus, Warts, Skin Disorders, Heel pain / Heel Spurs / Arch pain - plantar Fasciitis</p>
  <div class="abs btn" style="left:296px;top:1373px;width:190px;height:51px">READ MORE</div>

  <h3 class="abs service-title" style="left:642px;top:1213px">Specialised Treatments</h3>
  <div class="abs service-photo" style="left:640px;top:1272px;background:linear-gradient(135deg,#ece4de,#e5c6b3 55%,#f2f2f2)" role="img" aria-label="Gloved hands treating a toenail with an instrument"></div>
  <p class="abs service-text" style="left:860px;top:1270px;width:270px">Diabetic Management, Nail Surgery, Biomechanical Assessment, Gait Analysis, Orthotic Therapy</p>
  <div class="abs btn" style="left:858px;top:1373px;width:190px;height:51px">READ MORE</div>

  <div class="abs rule" style="top:1481px"></div>

  <!-- news -->
  <h2 class="abs section-title" style="top:1521px">LATEST <em>NEWS</em></h2>

  <div class="abs news-photo" style="left:77px;top:1589px;background:linear-gradient(160deg,#f2f2f2,#d9d4cc 60%,#b9a892)" role="img" aria-label="Physiotherapist stretching a patient's leg in a clinic"></div>
  <div class="abs news-photo" style="left:348px;top:1589px;background:linear-gradient(180deg,#8a8f92,#6f7a82 55%,#c9a98e)" role="img" aria-label="Bare feet walking through shallow water at the beach"></div>
  <div class="abs news-photo" style="left:619px;top:1589px;background:linear-gradient(135deg,#ffffff,#d7dbe6 45%,#e16d5a 70%,#ffffff);border:1px solid #ddd" role="img" aria-label="Foot diagram with the heel area highlighted in red"></div>
  <div class="abs news-photo" style="left:890px;top:1589px;background:linear-gradient(135deg,#f6f3f0,#e7d6cc 50%,#e59bb0)" role="img" aria-label="Clinician with a clipboard consulting an older patient"></div>

  <p class="abs news-title" style="left:79px;top:1747px">Lorem Ipsum is dummy text and simply printing.</p>
  <p class="abs news-title" style="left:350px;top:1747px">Lorem Ipsum is dummy text and simply printing.</p>
  <p class="abs news-title" style="left:621px;top:1747px">Lorem Ipsum is dummy text and simply printing.</p>
  <p class="abs news-title" style="left:892px;top:1747px">Lorem Ipsum is dummy text and simply printing.</p>

  <div class="abs news-date" style="left:79px;top:1804px"><svg width="14" height="14" viewBox="0 0 14 14" aria-hidden="true"><rect x="1" y="2" width="12" height="11" fill="none" stroke="#999"/><path d="M1 5h12M4 1v3M10 1v3" stroke="#999"/></svg>01 August 2016</div>
  <div class="abs news-date" style="left:350px;top:1804px"><svg width="14" height="14" viewBox="0 0 14 14" aria-hidden="true"><rect x="1" y="2" width="12" height="11" fill="none" stroke="#999"/><path d="M1 5h12M4 1v3M10 1v3" stroke="#999"/></svg>01 August 2016</div>
  <div class="abs news-date" style="left:621px;top:1804px"><svg width="14" height="14" viewBox="0 0 14 14" aria-hidden="true"><rect x="1" y="2" width="12" height="11" fill="none" stroke="#999"/><path d="M1 5h12M4 1v3M10 1v3" stroke="#999"/></svg>01 August 2016</div>
  <div class="abs news-date" style="left:892px;top:1804px"><svg width="14" height="14" viewBox="0 0 14 14" aria-hidden="true"><rect x="1" y="2" width="12" height="11" fill="none" stroke="#999"/><path d="M1 5h12M4 1v3M10 1v3" stroke="#999"/></svg>01 August 2016</div>

  <p class="abs news-text" style="left:79px;top:1830px">Lorem Ipsum is simply dummy text of the printing and type setting industry.</p>
  <p class="abs news-text" style="left:350px;top:1830px">Lorem Ipsum is simply dummy text of the printing and type setting industry.</p>
  <p class="abs news-text" style="left:621px;top:1830px">Lorem Ipsum is simply dummy text of the printing and type setting industry.</p>
  <p class="abs news-text" style="left:892px;top:1830px">Lorem Ipsum is simply dummy text of the printing and type setting industry.</p>

  <!-- as seen in -->
  <div class="abs seen"></div>
  <svg class="abs seen-label" viewBox="0 0 270 155" aria-hidden="true"><polygon points="0,0 226,0 270,77.5 226,155 0,155" fill="#4b2e9a"/></svg>
  <p class="abs seen-text">AS<br>SEEN IN</p>
  <div class="abs partner" style="left:306px;width:155px"></div>
  <div class="abs partner" style="left:510px;width:155px"></div>
  <div class="abs partner" style="left:712px;width:165px"></div>
  <div class="abs partner" style="left:935px;width:160px"></div>

  <!-- footer -->
  <svg class="abs footer-curve" width="1200" height="40" viewBox="0 0 1200 40" aria-hidden="true"><path d="M0 0 Q600 40 1200 0 L1200 40 L0 40z" fill="#323232"/></svg>
  <footer class="abs footer"></footer>
  <div class="abs footer-name">Brambleridge<br>Podiatry</div>

  <h4 class="abs footer-head" style="left:350px">Useful Links</h4>
  <ul class="abs footer-list" style="left:350px">
    <li><svg width="16" height="10" viewBox="0 0 16 10" aria-hidden="true"><path d="M0 5h14M10 1l4 4-4 4" stroke="#fff" stroke-width="1.6" fill="none"/></svg>Home</li>
    <li><svg width="16" height="10" viewBox="0 0 16 10" aria-hidden="true"><path d="M0 5h14M10 1l4 4-4 4" stroke="#fff" stroke-width="1.6" fill="none"/></svg>About</li>
    <li><svg width="16" height="10" viewBox="0 0 16 10" aria-hidden="true"><path d="M0 5h14M10 1l4 4-4 4" stroke="#fff" stroke-width="1.6" fill="none"/></svg>Services</li>
    <li><svg width="16" height="10" viewBox="0 0 16 10" aria-hidden="true"><path d="M0 5h14M10 1l4 4-4 4" stroke="#fff" stroke-width="1.6" fill="none"/></svg>Contact</li>
  </ul>

  <h4 class="abs footer-head" style="left:621px">Get In Touch</h4>
  <ul class="abs footer-list contact-list" style="left:621px;width:220px">
    <li><svg width="14" height="20" viewBox="0 0 14 20" aria-hidden="true" style="flex:none;margin-top:3px"><path d="M7 0C3 0 0 3 0 7c0 5 7 13 7 13s7-8 7-13c0-4-3-7-7-7zm0 10a3 3 0 110-6 3 3 0 010 6z" fill="#fff"/></svg>Suite 12 / 88 Harlow Street Melbourne 3000</li>
    <li style="font-weight:700"><svg width="18" height="18" viewBox="0 0 24 24" aria-hidden="true" style="flex:none;margin-top:3px"><path d="M5 2c2-1 3 0 4 2l2 4c.6 1.3 0 2.2-1 3l-1 1c1 3 4 6 7 7l1-1c.8-1 1.7-1.6 3-1l2 1c2 1 2 3 1 4-1 2-4 3-7 2C9 22 3 15 2 9 1 6 2 3 5 2z" fill="#fff"/></svg>1300 555 204</li>
    <li style="word-break:break-all"><svg width="18" height="14" viewBox="0 0 18 14" aria-hidden="true" style="flex:none;margin-top:5px"><rect x="1" y="1" width="16" height="12" fill="none" stroke="#fff" stroke-width="1.5"/><path d="M1 1l8 7 8-7" fill="none" stroke="#fff" stroke-width="1.5"/></svg>info@brambleridgepodiatry.net</li>
  </ul>

  <h4 class="abs footer-head" style="left:890px">Follow Us</h4>
  <ul class="abs footer-list social" style="left:890px">
    <li style="align-items:center"><span class="ring"><svg width="22" height="22" viewBox="0 0 24 24" aria-hidden="true"><path d="M10 14l4-4M8.5 11.5l-2 2a3.5 3.5 0 005 5l2-2M15.5 12.5l2-2a3.5 3.5 0 00-5-5l-2 2" fill="none" stroke="#323232" stroke-width="2" stroke-linecap="round"/></svg></span>Chatterbook</li>
    <li style="align-items:center"><span class="ring outline"><svg width="22" height="22" viewBox="0 0 24 24" aria-hidden="true"><path d="M10 14l4-4M8.5 11.5l-2 2a3.5 3.5 0 005 5l2-2M15.5 12.5l2-2a3.5 3.5 0 00-5-5l-2 2" fill="none" stroke="#fff" stroke-width="2" stroke-linecap="round"/></svg></span>Chirper</li>
  </ul>

  <div class="abs copyright">© Brambleridge Podiatry- 2016. All Rights Reserved.</div>
</div>
</body>
</html>
```